Website design for luxury private hair salon

I'm looking for someone to use my Logo and build me a website for my webpage www.corsetresses.com.au (You can have a look at it as it has every detail I need included on it already), however I want a fresh new appearance and it to look and feel super stylish.

I am thinking colours in black, with silver or white, beautiful hair images like the ones you'll see on the current webpage - the price list as per what you already see.

I will include a copy of my biz card on here, so you can see the feel of the card, and design a website with a similar feel. It is matt black with a foil silver.

Modern, but classic and fresh. I will also need you to be able to publish it to my URL for me as I have no idea how to do this. I need it up and running pronto!

The website will need to be able to be read clearly on all devices incluing smart phones and ipads. The URL is currently registered and hosted by Norvel Web

Thinking a Home Page - large logo etc and write up on who and what we offer
Services/Price List page - as per the price list on my current webpage
Contact Page - with a built in contact form.

Target Market(s)

Middle aged, fashionable, stylish women and men who enjoy luxury hair care and styling in an upmarket location.

Industry/Entity Type

Hair And Beauty

Number of Pages Required

3 page

Font styles to use
Other font styles liked:
• see my images for my current logo

Colors
000000
b2b2b2
a54499

Requirements
Must have
• Style
• Fast turnaround
• Be viewable on all devices, PC, ipads, smart phones
• Designer able to upload it so its a running website for me to my URL
Nice to have
• Just a really feminine, stylish website which is easy to read and shows some beautiful images of perfect hair
Should not have
• Browns, reds or orange colours.

```html
<!DOCTYPE html>
<html lang="en">
<head>
<meta charset="utf-8">
<title>Salon Services</title>
<link href="https://fonts.googleapis.com/css2?family=Raleway:wght@400;500;600&family=Playfair+Display:ital@1&display=swap" rel="stylesheet">
<style>
  :root {
    --ink: #1f1d21;
    --ink-deep: #141315;
    --plum: #a54499;
    --plum-soft: #b457a8;
    --silver: #b2b2b2;
    --white: #ffffff;
  }
  * { box-sizing: border-box; margin: 0; padding: 0; }
  html, body { width: 1200px; height: 1200px; overflow: hidden; background: var(--ink-deep); }
  body { font-family: "Raleway", sans-serif; color: var(--white); position: relative; }

  .hero-photo {
    position: absolute; left: 0; top: 0; width: 1200px; height: 800px;
    background:
      radial-gradient(ellipse 420px 380px at 560px 360px, #4a4448 0%, rgba(60,55,60,0.6) 45%, rgba(0,0,0,0) 80%),
      linear-gradient(180deg, #2c292d 0%, #262327 60%, #1e1c1f 100%);
  }

  .services { position: absolute; left: 0; top: 0; width: 1200px; height: 560px; text-align: center; }
  .section-title { font-size: 52px; font-weight: 400; letter-spacing: 0.5px; padding-top: 70px; }
  .section-title em { font-family: "Playfair Display", serif; font-style: italic; color: var(--plum-soft); }

  .service-row { display: flex; justify-content: center; gap: 0; }
  .service-row.primary { margin-top: 60px; }
  .service-row.secondary { margin-top: 60px; gap: 90px; }
  .service { width: 210px; display: flex; flex-direction: column; align-items: center; }
  .service svg { width: 52px; height: 52px; stroke: var(--plum-soft); fill: none; stroke-width: 2; stroke-linecap: round; stroke-linejoin: round; }
  .service-name { margin-top: 14px; font-size: 21px; font-weight: 500; }

  .cta-band {
    position: absolute; left: 0; top: 560px; width: 1200px; height: 240px;
    background: linear-gradient(90deg, rgba(165,68,153,0.93) 0%, rgba(165,68,153,0.88) 70%, rgba(180,87,168,0.92) 100%);
    display: flex; align-items: center; justify-content: space-between; padding: 0 110px 0 120px;
  }
  .cta-text { font-size: 32px; font-weight: 400; line-height: 1.3; width: 560px; }
  .cta-button {
    border: 2px solid var(--white); border-radius: 30px; padding: 16px 30px;
    font-size: 19px; font-weight: 600; letter-spacing: 0.3px; text-transform: uppercase; color: var(--white);
  }

  .contact { position: absolute; left: 0; top: 800px; width: 1200px; height: 400px; background: var(--ink); text-align: center; }
  .contact .section-title { padding-top: 60px; }
</style>
</head>
<body>
  <div class="hero-photo" role="img" aria-label="Dark, softly lit photograph of a woman with long flowing hair"></div>

  <section class="services">
    <h2 class="section-title">Our <em>services</em></h2>
    <div class="service-row primary">
      <div class="service">
        <svg viewBox="0 0 52 52"><circle cx="14" cy="40" r="5"/><circle cx="24" cy="42" r="5"/><path d="M17 36 L40 8 M21 38 L42 12"/></svg>
        <span class="service-name">Hair Cuts</span>
      </div>
      <div class="service">
        <svg viewBox="0 0 52 52"><path d="M8 46 L26 26"/><path d="M22 22 L32 32 L44 20 L34 10 Z"/><path d="M34 10 L40 4 M38 14 L44 8 M42 18 L48 12"/></svg>
        <span class="service-name">Colouring</span>
      </div>
      <div class="service">
        <svg viewBox="0 0 52 52"><path d="M14 38 L36 10 L44 16 L22 44 Z"/><path d="M14 38 L10 46 L22 44"/><path d="M6 48 H30"/></svg>
        <span class="service-name">Highlighting</span>
      </div>
      <div class="service">
        <svg viewBox="0 0 52 52"><rect x="16" y="20" width="20" height="26" rx="3"/><path d="M16 28 H36"/><path d="M26 20 V14"/><circle cx="26" cy="10" r="3"/></svg>
        <span class="service-name">Extensions</span>
      </div>
      <div class="service">
        <svg viewBox="0 0 52 52"><path d="M20 4 L22 36 M28 4 L26 36"/><path d="M22 36 L20 46 M26 36 L34 46"/></svg>
        <span class="service-name">Straightening</span>
      </div>
    </div>
    <div class="service-row secondary">
      <div class="service">
        <svg viewBox="0 0 52 52"><path d="M14 40 C10 20 16 8 26 8 C36 8 42 20 38 40"/><circle cx="26" cy="24" r="9"/><path d="M14 46 C16 38 36 38 38 46"/></svg>
        <span class="service-name">Bridal Treatments</span>
      </div>
      <div class="service">
        <svg viewBox="0 0 52 52"><rect x="8" y="14" width="14" height="32" rx="2"/><rect x="28" y="10" width="16" height="36" rx="2"/><path d="M8 22 H22 M28 20 H44"/><path d="M33 30 L36 34 L40 28"/></svg>
        <span class="service-name">Products &amp; Advice</span>
      </div>
    </div>
  </section>

  <section class="cta-band">
    <p class="cta-text">Wana do something with with your Hairs? So Meet us</p>
    <span class="cta-button">Book an Appointment</span>
  </section>

  <section class="contact">
    <h2 class="section-title">Contact <em>us</em></h2>
  </section>
</body>
</html>
```